Letter design, envelope design, and more

Hello, we the Tavrin Gmbh are looking for our shop. Letter C5. Design does not have to be like a business card, so it can have straight lines. Only the color is important. The logo is the text under TaVRin omit.It should not be playful but Profesionel

Font styles to use
Sans Serif

Colors
0555a3
3176b5
85abd2
85cae6
34a7d8
0792cd
cee9f5
cfdfed
000000

Requirements
Must have
• Color like business card, Please, with the text under TaVRin, Correct address Lindmattstr. 4 Zip code 9517 Seewil, as well as Couvert Without addressing only design and logo with TaVrn
Nice to have
• more writing articles
Should not have
• Not too colored, Text under TaVRin, bright colors

```html
<!DOCTYPE html>
<html lang="de">
<head>
<meta charset="utf-8">
<title>Tavrin Gmbh – Briefpapier und Couvert</title>
<link rel="stylesheet" href="https://fonts.googleapis.com/css2?family=Source+Sans+3:wght@400;600&family=Arimo:wght@700&display=swap">
<style>
  :root{
    --bg:#dedede;
    --paper:#ffffff;
    --navy:#1f3566;
    --brand-blue:#3176b5;
    --line-blue:#34a7d8;
    --band-blue:#3176b5;
    --text:#3a3a3a;
    --ink:#000000;
  }
  *{margin:0;padding:0;box-sizing:border-box}
  html,body{width:1200px;height:800px;overflow:hidden;background:var(--bg)}
  body{position:relative;font-family:"Source Sans 3",sans-serif;color:var(--text)}

  .sheet{position:absolute;background:var(--paper);box-shadow:0 1px 4px rgba(0,0,0,.15)}
  .letter{left:80px;top:86px;width:486px;height:628px}
  .envelope{left:605px;top:350px;width:515px;height:364px}
  .envelope-flap{position:absolute;left:605px;top:286px;width:515px;height:66px}

  .brand{position:absolute;display:flex;align-items:center;gap:6px}
  .brand-mark{width:30px;height:30px;background:var(--navy)}
  .brand-name{font-family:"Source Sans 3",sans-serif;font-weight:600;font-size:22px;letter-spacing:.5px;color:var(--navy)}
  .letter .brand{left:50px;top:38px}
  .envelope .brand{left:40px;top:28px}

  .salutation{position:absolute;left:50px;top:139px;font-family:"Arimo",sans-serif;font-weight:700;font-size:11.5px;color:var(--ink)}
  .letter-body{position:absolute;left:50px;top:165px;width:386px;font-size:10.2px;line-height:12.4px;text-align:justify;color:var(--text)}
  .letter-body p{margin-bottom:12.4px}
  .signature{position:absolute;left:50px;top:486px;width:76px;height:36px;background:linear-gradient(90deg,#e9e9e9,#f4f4f4);border-radius:3px}

  .footer{position:absolute;left:0;right:0;bottom:0;height:24px}
  .contacts{position:absolute;left:50px;top:0;display:flex;gap:6px;font-size:7.4px;color:var(--ink);align-items:center;white-space:nowrap}
  .contacts span{display:flex;align-items:center;gap:2px}
  .contacts svg{width:6px;height:6px;fill:var(--brand-blue)}
  .rule{position:absolute;left:0;right:0;top:11px;height:1px;background:var(--line-blue)}
  .web{position:absolute;right:48px;top:6px;padding:0 3px;background:var(--paper);font-size:7.6px;letter-spacing:1.8px;color:var(--line-blue)}
  .band{position:absolute;left:0;right:0;bottom:0;height:5px;background:var(--band-blue)}
  .envelope .contacts{left:40px}
</style>
</head>
<body>

<section class="sheet letter">
  <div class="brand"><span class="brand-mark"></span><span class="brand-name">TAVRIN</span></div>

  <h2 class="salutation">Dear Mr. Keller,</h2>
  <div class="letter-body">
    <p>Lorem Ipsum is simply dummy text of the printing and typesetting industry. Lorem Ipsum has been the industry's standard dummy text ever since the 1500s, when an unknown printer took a galley of type and scrambled it to make a type specimen book. It has survived not only five centuries, but also the leap into electronic typesetting, remaining essentially unchanged.</p>
    <p>The standard chunk of Lorem Ipsum used since the 1500s is reproduced below for those interested. Sections 1.10.32 and 1.10.33 from "de Finibus Bonorum et Malorum" by Cicero are also reproduced in their exact original form, accompanied by English versions from the 1914 translation by H. Rackham</p>
    <p>Lorem Ipsum is simply dummy text of the printing and typesetting industry. Lorem Ipsum has been the industry's standard dummy text ever since the 1500s, when an unknown printer took a galley of type and scrambled it to make a type specimen book. It has survived not only five centuries, but also the leap into electronic typesetting, remaining essentially unchanged. It was popularised in the</p>
    <p>The standard chunk of Lorem Ipsum used since the 1500s is reproduced below for those interested. Sections 1.10.32 and 1.10.33 from "de Finibus Bonorum et Malorum" by Cicero are also reproduced in their exact original form, accompanied by English versions from the 1914 translation by H. Rackham</p>
    <p>The standard chunk of Lorem Ipsum used since the 1500s is reproduced below for those interested. Sections 1.10.32 and 1.10.33 from "de Finibus Bonorum et Malorum" by Cicero are</p>
  </div>
  <div class="signature" role="img" aria-label="Handwritten signature"></div>

  <footer class="footer">
    <div class="contacts">
      <span><svg viewBox="0 0 10 10"><path d="M2 0l2 2-1 1.5q1 2 3.5 3.5L8 6l2 2-1.5 2Q1 9 0 1.5z"/></svg>+41 71 555 20 14</span>
      <span><svg viewBox="0 0 10 10"><path d="M0 2h10v6H0zM0 2l5 3.5L10 2"/></svg>info@tavrin.ch</span>
      <span><svg viewBox="0 0 10 10"><path d="M5 0a3.5 3.5 0 0 1 3.5 3.5C8.5 6 5 10 5 10S1.5 6 1.5 3.5A3.5 3.5 0 0 1 5 0zm0 2a1.5 1.5 0 1 0 0 3 1.5 1.5 0 0 0 0-3z"/></svg>Lindmattstr. 4 &nbsp;9517 Seewil,</span>
    </div>
    <div class="rule"></div>
    <div class="web">www.tavrin.ch</div>
    <div class="band"></div>
  </footer>
</section>

<svg class="envelope-flap" viewBox="0 0 515 66" aria-hidden="true">
  <path d="M3 66 L3 24 Q3 9 20 7 Q258 -6 495 7 Q512 9 512 24 L512 66 Z" fill="var(--band-blue)"/>
</svg>

<section class="sheet envelope">
  <div class="brand"><span class="brand-mark"></span><span class="brand-name">TAVRIN</span></div>
  <footer class="footer">
    <div class="contacts">
      <span><svg viewBox="0 0 10 10"><path d="M2 0l2 2-1 1.5q1 2 3.5 3.5L8 6l2 2-1.5 2Q1 9 0 1.5z"/></svg>+41 71 555 20 14</span>
      <span><svg viewBox="0 0 10 10"><path d="M0 2h10v6H0zM0 2l5 3.5L10 2"/></svg>info@tavrin.ch</span>
      <span><svg viewBox="0 0 10 10"><path d="M5 0a3.5 3.5 0 0 1 3.5 3.5C8.5 6 5 10 5 10S1.5 6 1.5 3.5A3.5 3.5 0 0 1 5 0zm0 2a1.5 1.5 0 1 0 0 3 1.5 1.5 0 0 0 0-3z"/></svg>Lindmattstr. 4 &nbsp;9517 Seewil,</span>
    </div>
    <div class="rule"></div>
    <div class="web">www.tavrin.ch</div>
    <div class="band"></div>
  </footer>
</section>

</body>
</html>
```